Stage Design Company Business Card

We are looking to step up up our business card design for our team.

We are a Full service Design and Consultation company for Stage and TV with an emphasis in Theatrical Lighting.

We like our materials to be clean and modern with solid colors free of patterns and gradients. Our brand consists of 4 primary colors Purple, Black, Grey, and White. Provided is our Word Mark as well as our Symbol Logo.

We would like our cards to leave an impression beyond the information, show our attention to design and detail, and make our marks an easily recognized feature (together or apart) for our clients.

We need a warm approachable comfortable feel for some clients, and a professional flair for the board member type clients.

Attached are our brand elements, and our existing cards to give a sense of our style and a glipse at the information we provide on our cards.

Target Market(s)

broad client base from church leaders to high school teachers and architects.

Industry/Entity Type

Business

Contact Information for Business Card

We format our phone number with periods not parenthesis or dashes. Information will be edited for each of our team members, and team member specific cards are not part of this scope, but rather a template so to speak.

Font styles to use
Sans Serif

Colors
6b449b
ffffff
000000
333333
aaaaaa

Requirements
Must have
• Wordmark and logo mark present (does not need to exist on the same side of card)
• Brand Colors,
• Name, Phone, Email, Address.
• Unique choices that make someone stop and take a second look
Nice to have
• It would be nice to somehow convey what we DO, as our brand name does not lend itself to this, outside of an obvious tagline though.....
• social media if not crowded. all of our handles match (instagram, twitter, facebook)
Should not have
• "clipart"

```html
<!DOCTYPE html>
<html lang="en">
<head>
<meta charset="utf-8">
<title>Merrow Entertainment – Business Card</title>
<link rel="stylesheet" href="https://fonts.googleapis.com/css2?family=Questrial&display=swap">
<style>
  :root {
    --brand-purple: #3a2a6d;
    --paper-white: #ffffff;
    --ink-black: #1a1a1a;
    --ink-grey: #333333;
    --soft-grey: #aaaaaa;
    --mark-light: #e9e9ec;
    --stage-bg: #7a7a7a;
  }
  * { box-sizing: border-box; margin: 0; padding: 0; }
  html, body {
    width: 1200px;
    height: 1200px;
    overflow: hidden;
    background: var(--stage-bg);
    font-family: "Questrial", "Century Gothic", sans-serif;
  }
  .canvas {
    position: relative;
    width: 1200px;
    height: 1200px;
  }
  .card {
    position: absolute;
    left: 150px;
    width: 900px;
    height: 525px;
    overflow: hidden;
  }
  .card--front { top: 50px; background: var(--paper-white); }
  .card--back  { top: 625px; background: var(--brand-purple); }

  .wordmark {
    position: absolute;
    font-size: 44px;
    letter-spacing: 0.62em;
    line-height: 1;
    white-space: nowrap;
  }
  .card--front .wordmark {
    left: 69px;
    top: 72px;
    color: var(--brand-purple);
  }
  .card--back .wordmark {
    left: 120px;
    top: 205px;
    color: var(--paper-white);
  }
  .tagline {
    position: absolute;
    left: 120px;
    top: 300px;
    font-size: 15px;
    letter-spacing: 1.05em;
    color: var(--paper-white);
    white-space: nowrap;
  }

  .person {
    position: absolute;
    left: 69px;
    top: 152px;
  }
  .person__name {
    font-size: 41px;
    color: var(--ink-black);
    letter-spacing: 0.02em;
    -webkit-text-stroke: 0.6px var(--ink-black);
    line-height: 1.1;
  }
  .person__title {
    font-size: 23px;
    color: var(--ink-grey);
    line-height: 1.2;
  }

  .contact-list {
    position: absolute;
    left: 69px;
    top: 261px;
    list-style: none;
    font-size: 28px;
    color: var(--ink-grey);
  }
  .contact-list li {
    display: flex;
    align-items: center;
    height: 35px;
  }
  .contact-list svg {
    width: 24px;
    height: 24px;
    margin-right: 12px;
    flex: none;
  }
  .address {
    position: absolute;
    left: 69px;
    top: 383px;
    font-size: 28px;
    line-height: 36px;
    color: var(--ink-grey);
    font-style: normal;
  }

  .symbol-field {
    position: absolute;
    width: 380px;
    height: 380px;
    border-radius: 50%;
  }
  .card--front .symbol-field {
    left: 600px;
    top: 75px;
    background: var(--brand-purple);
  }
  .card--back .symbol-field {
    left: 570px;
    top: 75px;
    background: var(--mark-light);
  }
</style>
</head>
<body>
<main class="canvas">

  <section class="card card--front" aria-label="Card front">
    <div class="wordmark">MERROW</div>

    <div class="person">
      <h1 class="person__name">Noel R Hartley</h1>
      <p class="person__title">JOB TITLE</p>
    </div>

    <ul class="contact-list">
      <li>
        <svg viewBox="0 0 24 24" fill="none" stroke="#3a2a6d" stroke-width="1.8" stroke-linejoin="round" aria-hidden="true">
          <path d="M5 3h4l2 5-2.5 1.5a11 11 0 0 0 6 6L16 13l5 2v4a2 2 0 0 1-2 2A17 17 0 0 1 3 5a2 2 0 0 1 2-2z"/>
        </svg>
        555.014.2290
      </li>
      <li>
        <svg viewBox="0 0 24 24" fill="none" stroke="#3a2a6d" stroke-width="1.8" stroke-linejoin="round" aria-hidden="true">
          <rect x="2.5" y="5" width="19" height="14" rx="1"/>
          <path d="M3 6l9 7 9-7"/>
        </svg>
        noel@merrow-e.com
      </li>
      <li>
        <svg viewBox="0 0 24 24" fill="none" stroke="#3a2a6d" stroke-width="1.6" aria-hidden="true">
          <circle cx="12" cy="12" r="9.5"/>
          <ellipse cx="12" cy="12" rx="4.2" ry="9.5"/>
          <path d="M2.5 12h19M4 7h16M4 17h16"/>
        </svg>
        www.merrow-e.com
      </li>
    </ul>

    <address class="address">
      18 N Elm Ave<br>
      Larkfield, AZ 85099
    </address>

    <div class="symbol-field"></div>
  </section>

  <section class="card card--back" aria-label="Card back">
    <div class="wordmark">MERROW</div>
    <div class="tagline">ENTERTAINMENT</div>
    <div class="symbol-field"></div>
  </section>

</main>
</body>
</html>
```